Trifold Leaflet - Osteopathy

Trifold Leaflet (A4 size paper) to provide information and promote an established English seafront osteopathy clinic.
I would like a simple modern design to reflect the seafront location and the caring nature of osteopathy treatment. The design needs to be not be generic or too corporate.
At the top of the front page in a large font should be the word "Osteopathy" as it will be displayed in a rack of leaflets (photo attached) and needs to be eye-catching.
I have attached a logo file and some examples of the kinds of designs that I like- but i'm very open to your expert ideas!
Also attached is a photo of the location- a bit of an ugly building but right on the beach, it would be great if this location could be emphasized!
The Word files: Leaflets word-inside.doc & Leaflets word-outside.doc uploaded show the content that I'd like- this is definitely not set in stone and I appreciate that less content is probably needed. Feel free to include/leave out whatever you feel is right.
More info on the practice can be found on my website:
www.marlowbayosteo.com
The pixelharbor images are ones that I have previously bought the rights to use, but only use them if you think they suit you design- I have included them i case they are of use to you.
Target Market(s)
Any adult.
Industry/Entity Type
Building
Look and feel

```html
<!DOCTYPE html>
<html lang="en">
<head>
<meta charset="utf-8">
<title>Osteopathy Trifold Leaflet – Inside Spread</title>
<link rel="stylesheet" href="https://fonts.googleapis.com/css2?family=Open+Sans:wght@400;600;700&display=swap">
<style>
  :root {
    --brand-red: #b5242f;
    --paper: #ffffff;
    --paper-shade: #f4f4f4;
    --ink: #4a4a4a;
    --backdrop: #e9e9ea;
    --photo-light: #eeeae6;
    --photo-mid: #d9cfc6;
    --photo-deep: #b9a89a;
  }
  * { box-sizing: border-box; margin: 0; padding: 0; }
  html, body {
    width: 1200px; height: 795px; overflow: hidden;
    background: var(--backdrop);
    font-family: "Open Sans", Arial, sans-serif;
  }
  body { position: relative; }
  .leaflet {
    position: absolute; left: 75px; top: 26px;
    width: 1050px; height: 743px;
    display: flex;
    overflow: hidden;
    box-shadow: 0 6px 24px rgba(0,0,0,.12);
  }
  .panel {
    position: relative;
    width: 350px; height: 100%;
    overflow: hidden;
    background: var(--paper);
  }
  .panel--middle { background: var(--paper-shade); }
  .panel--visit { background: var(--brand-red); color: #fff; padding: 40px 34px; }

  .treatment-photo {
    position: absolute; left: 0; top: 0; width: 350px;
    background: linear-gradient(120deg, var(--photo-light) 0%, var(--photo-mid) 55%, var(--photo-deep) 100%);
  }
  .treatment-photo--left { height: 280px; }
  .treatment-photo--middle {
    height: 330px;
    background: linear-gradient(120deg, var(--photo-mid) 0%, var(--photo-deep) 60%, var(--photo-light) 100%);
  }

  .panel__content { position: absolute; left: 34px; right: 34px; }
  .panel--left .panel__content { top: 306px; }
  .panel--middle .panel__content { top: 356px; }

  .section-title {
    color: var(--brand-red);
    font-weight: 600;
    font-size: 20px; line-height: 1.15;
    text-transform: uppercase;
    padding-bottom: 9px;
    border-bottom: 2px dotted var(--brand-red);
    margin-bottom: 13px;
  }
  .body-copy {
    color: var(--ink);
    font-size: 12px; line-height: 1.5;
    margin-bottom: 10px;
  }

  .visit-title {
    font-weight: 400; font-size: 24px;
    text-transform: uppercase; letter-spacing: .5px;
    margin-bottom: 18px;
  }
  .visit-step {
    padding-bottom: 14px; margin-bottom: 16px;
    border-bottom: 1px dotted rgba(255,255,255,.6);
  }
  .visit-step:last-of-type { border-bottom: none; }
  .visit-step__head {
    display: flex; align-items: center; gap: 12px;
    margin-bottom: 8px;
  }
  .visit-step__number {
    width: 30px; height: 30px; border-radius: 50%;
    border: 2px solid #fff;
    display: flex; align-items: center; justify-content: center;
    font-size: 16px; font-weight: 600;
  }
  .visit-step__name {
    font-size: 14px; text-transform: uppercase; letter-spacing: .4px;
  }
  .visit-step__text, .visit-closing {
    font-size: 12px; line-height: 1.5;
  }
</style>
</head>
<body>
  <main class="leaflet">
    <section class="panel panel--left">
      <div class="treatment-photo treatment-photo--left" role="img" aria-label="Photo of a patient lying on a treatment couch in a bright clinic"></div>
      <div class="panel__content">
        <h2 class="section-title">Natural, drug free<br>pain relief</h2>
        <p class="body-copy">Much of the pain and disability we suffer stems from abnormalities in our body's structure and function.</p>
        <p class="body-copy">Osteopathy treats problems related to the musculoskeletal system, muscles, ligaments, nerves and joints, and helps the body's natural healing ability to correct itself and relieve the pain caused by dysfunction.</p>
        <p class="body-copy">When the body is balanced and efficient, just like a tuned engine, it will function with minimum wear and tear, requiring less energy to operate correctly.</p>
      </div>
    </section>

    <section class="panel panel--middle">
      <div class="treatment-photo treatment-photo--middle" role="img" aria-label="Photo of an osteopath gently treating a patient's neck"></div>
      <div class="panel__content">
        <h2 class="section-title">Osteopathy is regulated<br>and safe</h2>
        <p class="body-copy">Osteopathy is one of only two complementary and alternative medicines (CAMs) that are regulated under UK law. This regulation works in much the same way as regulation for medical doctors.</p>
        <p class="body-copy">The ORB regulates the Osteopathic profession in the UK, maintaining a Statutory Register of those entitled to practise. Only practitioners meeting the high standards of safety and competency are eligible to join this register. All Osteopaths are required to undertake a certain amount of CPD (Continuing Professional Development) each year to keep up to date with new research and practise within the profession.</p>
      </div>
    </section>

    <section class="panel panel--visit">
      <h2 class="visit-title">Your first visit</h2>
      <div class="visit-step">
        <div class="visit-step__head"><span class="visit-step__number">1</span><span class="visit-step__name">Medical history</span></div>
        <p class="visit-step__text">On your first visit, we will ask you lots of questions to build up a detailed medical history. Your past medical history can often be relevant to current problems you are experiencing and may be discussed.</p>
      </div>
      <div class="visit-step">
        <div class="visit-step__head"><span class="visit-step__number">2</span><span class="visit-step__name">Assessment</span></div>
        <p class="visit-step__text">Based on your medical history, we will perform some tests to help form a diagnosis of your current condition. Typical tests include range and quality of joint movements, tenderness to palpation, muscle tone and strength, reflexes.</p>
      </div>
      <div class="visit-step">
        <div class="visit-step__head"><span class="visit-step__number">3</span><span class="visit-step__name">Treatment</span></div>
        <p class="visit-step__text">The detailed examination enables the Osteopath to diagnose safely and choose the right treatment to address the causes of the patient's symptoms. Treatment involves gentle, manual techniques – easing pain, reducing swelling and improving mobility. Osteopathy is a 'package' of care that includes skilled mobilising and manipulative techniques, reinforced by guidance on diet and exercise.</p>
      </div>
      <p class="visit-closing">For further information please contact us.<br>We are here to help!</p>
    </section>
  </main>
</body>
</html>
```